Oil Field Service company needs professional business cards

Looking to clean up our current company business cards and look a little more professional. Brenwick Casing Services is a US based company that services the oil field. We deal with engineers, managers and oil rigs....................................................................................................................................................................................................................................................................................................................................................................................................

Target Market(s)

Oil and Gas professionals

Industry/Entity Type

Oil And Gas

Contact Information for Business Card

See attached photo as example

Font styles to use
Sans Serif

Colors
ec1f27

Requirements
Must have
• Company Logo, Name, Title, Cell, Office, Fax, Email.
• See attached photo
Nice to have
• External CRT, Internal CRT, Casing Crews, Torque Turn, Laydown Machine
Should not have
• Do not introduce any new pictures and keep it professional looking

```html
<!DOCTYPE html>
<html lang="en">
<head>
<meta charset="utf-8">
<title>Brenwick Casing Services – Business Card</title>
<link rel="stylesheet" href="https://fonts.googleapis.com/css2?family=Source+Sans+3:wght@400;600;700&family=Ubuntu:wght@400&display=swap">
<style>
  :root {
    --page-bg: #e9e9e9;
    --card-white: #fbfbfb;
    --brand-red: #e31b23;
    --ink-dark: #3d4852;
    --ink-soft: #4a4f55;
    --white: #ffffff;
  }
  * { margin: 0; padding: 0; box-sizing: border-box; }
  html, body {
    width: 1200px; height: 1200px; overflow: hidden;
    background: var(--page-bg);
    font-family: "Source Sans 3", "Helvetica Neue", Arial, sans-serif;
  }
  .card {
    position: absolute; left: 80px; top: 307px;
    width: 1040px; height: 585px;
    display: flex;
    box-shadow: 0 12px 28px rgba(0,0,0,0.12);
  }
  .card-front {
    position: relative; width: 520px; height: 100%;
    background: var(--card-white);
  }
  .card-info {
    position: relative; width: 520px; height: 100%;
    background: var(--brand-red); color: var(--white);
  }
  .wordmark {
    position: absolute; left: 0; right: 0; top: 110px;
    text-align: center; color: var(--ink-dark);
    font-weight: 700; font-size: 40px; line-height: 1.15;
    letter-spacing: 0.04em; text-transform: uppercase;
  }
  .services {
    position: absolute; left: 0; right: 0; top: 295px;
    text-align: center; list-style: none;
    font-family: "Ubuntu", "Source Sans 3", sans-serif;
    font-size: 21px; color: var(--ink-soft); letter-spacing: 0.03em;
  }
  .services li { height: 37px; line-height: 37px; }
  .person { position: absolute; left: 57px; top: 121px; }
  .person-name { font-size: 37px; font-weight: 700; line-height: 44px; }
  .person-title { font-size: 21px; font-weight: 400; line-height: 26px; }
  .contact { position: absolute; left: 57px; top: 0; width: 440px; list-style: none; }
  .contact li {
    position: absolute; left: 0; display: flex; align-items: center;
    font-size: 21px; white-space: nowrap;
  }
  .contact .num { font-weight: 700; font-size: 22px; }
  .contact svg { width: 22px; height: 22px; margin-right: 21px; flex: none; fill: var(--white); }
</style>
</head>
<body>
  <div class="card">
    <section class="card-front">
      <div class="wordmark">Brenwick<br>Casing Services</div>
      <ul class="services">
        <li>External CRT . Internal CRT</li>
        <li>Casing Crews . Torque Turn</li>
        <li>Laydown Machine</li>
      </ul>
    </section>
    <section class="card-info">
      <div class="person">
        <h1 class="person-name">Cody Harlan</h1>
        <p class="person-title">AREA MANAGER</p>
      </div>
      <ul class="contact">
        <li style="top:254px">
          <svg viewBox="0 0 24 24"><path d="M12 2a7 7 0 0 0-7 7c0 5 7 13 7 13s7-8 7-13a7 7 0 0 0-7-7zm0 9.5A2.5 2.5 0 1 1 12 6.5a2.5 2.5 0 0 1 0 5z"/></svg>
          <span>ridgeton, OK 73850</span>
        </li>
        <li style="top:304px">
          <svg viewBox="0 0 24 24"><path d="M7 1h10a2 2 0 0 1 2 2v18a2 2 0 0 1-2 2H7a2 2 0 0 1-2-2V3a2 2 0 0 1 2-2zm0 3v11h10V4zm5 14a1.3 1.3 0 1 0 0 2.6A1.3 1.3 0 0 0 12 18z"/></svg>
          <span class="num">555 214 5700</span>
        </li>
        <li style="top:337px">
          <svg viewBox="0 0 24 24"><path d="M6.6 10.8a15.1 15.1 0 0 0 6.6 6.6l2.2-2.2a1 1 0 0 1 1-.25 11.4 11.4 0 0 0 3.6.57 1 1 0 0 1 1 1V20a1 1 0 0 1-1 1A17 17 0 0 1 3 4a1 1 0 0 1 1-1h3.5a1 1 0 0 1 1 1c0 1.25.2 2.45.57 3.57a1 1 0 0 1-.25 1z"/></svg>
          <span class="num">555 381 7496</span>
        </li>
        <li style="top:370px">
          <svg viewBox="0 0 24 24"><path d="M6 2h12v5H6zM4 8h16a2 2 0 0 1 2 2v7h-4v5H6v-5H2v-7a2 2 0 0 1 2-2zm4 8v4h8v-4zm10-5a1 1 0 1 0 0 2 1 1 0 0 0 0-2z"/></svg>
          <span class="num">555 214 3230</span>
        </li>
        <li style="top:421px">
          <svg viewBox="0 0 24 24"><path d="M2 5h20v14H2zm2 2v.4l8 5.6 8-5.6V7zm0 2.8V17h16V9.8l-8 5.6z"/></svg>
          <span>codyharlan@brenwickservice.com</span>
        </li>
      </ul>
    </section>
  </div>
</body>
</html>
```